Heron Loan Partners Business Card

We need a business card design for our mortgage servicing company. In addition to servicing the loans of homeowners, we help homeowners with purchasing their homes and any mortgage refinancing. We would like to see designs that use the colors in the logo attached below (gold-ish yellow and navy blue), and any other design you deem fit! The design should communicate a simpler life with smart mortgages provided by Heron.

```html
<!DOCTYPE html>
<html lang="en">
<head>
<meta charset="UTF-8">
<title>Heron Loan Partners – Business Card</title>
<link href="https://fonts.googleapis.com/css2?family=Playfair+Display:wght@700;900&family=Arimo:wght@400&display=swap" rel="stylesheet">
<style>
  :root {
    --navy: #262054;
    --gold: #e0b23a;
    --white: #ffffff;
    --ink: #2a2a2a;
    --backdrop: #c4c4c4;
  }
  * { margin: 0; padding: 0; box-sizing: border-box; }
  html, body { width: 1200px; height: 800px; overflow: hidden; }
  body {
    background: var(--backdrop);
    font-family: "Arimo", Arial, sans-serif;
    position: relative;
  }
  .card {
    position: absolute;
    top: 250px;
    width: 525px;
    height: 300px;
    border-radius: 18px;
    overflow: hidden;
    border-bottom: 2px solid var(--gold);
    box-shadow: 0 10px 24px rgba(0,0,0,0.25);
  }
  .card--front { left: 50px; background: var(--white); }
  .card--back { left: 625px; background: var(--navy); }

  .holder { position: absolute; left: 34px; top: 88px; }
  .holder__name {
    font-family: "Playfair Display", Georgia, serif;
    font-weight: 700;
    font-size: 22px;
    color: var(--gold);
    line-height: 1;
  }
  .holder__title {
    font-size: 11px;
    color: var(--navy);
    letter-spacing: 0.3px;
    margin-top: 5px;
  }

  .contact-band {
    position: absolute;
    left: 0; top: 148px;
    width: 320px; height: 66px;
    background: var(--navy);
    border-radius: 0 33px 33px 0;
    padding: 8px 0 0 34px;
  }
  .contact-band__row {
    display: flex; align-items: center; gap: 7px;
    color: var(--white);
    font-size: 13px;
    line-height: 16.5px;
  }
  .contact-band__icon { width: 11px; height: 11px; flex: none; }

  .address {
    position: absolute; left: 34px; top: 232px;
    font-size: 13px; line-height: 17px; color: var(--ink);
  }

  .brand {
    position: absolute;
    font-family: "Playfair Display", Georgia, serif;
    font-weight: 900;
    white-space: nowrap;
    line-height: 1;
  }
  .brand--front { right: 30px; top: 104px; font-size: 28px; color: var(--navy); }
  .brand--back {
    left: 50%; top: 50%; transform: translate(-50%, -50%);
    font-size: 54px; color: var(--gold);
  }
</style>
</head>
<body>
  <section class="card card--front" aria-label="Business card front">
    <div class="holder">
      <p class="holder__name">Daniel Whitford</p>
      <p class="holder__title">MANAGING DIRECTOR</p>
    </div>

    <p class="brand brand--front">Heron Mortgage</p>

    <div class="contact-band">
      <p class="contact-band__row">
        <svg class="contact-band__icon" viewBox="0 0 12 12" aria-hidden="true"><path d="M2.5 1 L4.5 1 L5.3 3.6 L4 4.6 Q5 7 7.4 8 L8.4 6.7 L11 7.5 L11 9.5 Q11 11 9.5 11 Q1 10.5 1 2.5 Q1 1 2.5 1 Z" fill="#e0b23a"/></svg>
        044-987 654 321
      </p>
      <p class="contact-band__row">
        <svg class="contact-band__icon" viewBox="0 0 12 12" aria-hidden="true"><rect x="0.5" y="2" width="11" height="8" fill="#e0b23a"/><path d="M0.5 2 L6 6.5 L11.5 2" stroke="#262054" stroke-width="1" fill="none"/></svg>
        hello@heronloans.com
      </p>
      <p class="contact-band__row">
        <svg class="contact-band__icon" viewBox="0 0 12 12" aria-hidden="true"><circle cx="6" cy="6" r="5.5" fill="#e0b23a"/><path d="M0.5 6 H11.5 M6 0.5 V11.5 M6 0.5 Q2.5 6 6 11.5 M6 0.5 Q9.5 6 6 11.5" stroke="#262054" stroke-width="0.8" fill="none"/></svg>
        www.heronloans.com
      </p>
    </div>

    <p class="address">58, Harbor View Lane, Suite 4<br>30127, Bayford</p>
  </section>

  <section class="card card--back" aria-label="Business card back">
    <p class="brand brand--back">Heron Mortgage</p>
  </section>
</body>
</html>
```